Pull Up Banner - Recruitment Company

We would like a design for a pull up banner.

For context: we are a recruitment business. We specialise in helping people in healthcare industry to find jobs in Australia.

I have come up with several ideas and text for the banner. Feel free to use the following as you see appropriate:

- Our logo (see attached)
- 'Healthcare Recruitment Agency'
- Some sort of imagine / cartoon of medical professionals (ie. doctor, nurse, physiotherapist, speech pathologist). A cartoon is more friendly than committing to a photo
- 'Empowering your next career move'
- 'Discover tailored opportunities based on your career preferences'
- Dot points (allied health, nursing, medical imaging)
- Contact info at the bottom including our website (www.quellastaffing.com.au, our Instagram handle @quellastaffing, Mobile: XXXX XXX XXX. The title section for contact information could be 'Get in touch:'

Feel free to submit a couple of designs and we can merge aspects that look good on your designs and find the perfect fit.
Thank you
Updates

Hello,

Thank you for your initial submissions to this project. I appreciate the time you've invested.

After reviewing the first attempt, I'd like to share some feedback and initial observations:

- Professionalism and engagement: Is the overall appearance of the banner professional? It's crucial that we have a high-quality design as this will represent our business.

- Image selection: The image (whether cartoon or real people) appears quite generic. Please consider submitting the banner with a few different photos in the middle for us to choose from. Ensure the image is a good fit and not simply a generic stock photo.

- Contact section: Kindly remove the phone number; we no longer wish to include it on the banner. Instead, please include our website (www.quellastaffing.com.au) and Instagram handle (@quellastaffing).

- Color scheme: White, black, and red/pink are preferred, or alternatively, blue. However, please avoid incorporating too many different colors as it may detract from the professional appearance.

We will be printing the design on a banner and require it to look professional and engaging.

Thank you once again for your submissions. I hope the feedback provided above is helpful.

Warm regards,

Target Market(s)

Allied Health Australia

Font styles to use
Serif

Colors
0054AA
0677BA
7BADD7
CADEEF
E8F1F8
0094D4
00A9DD
6FCCEA
C7EBF8
E9F6FB
EB3D1F
EC4F4E
F09395
F8D3D4
FCEDEE

```html
<!DOCTYPE html>
<html lang="en">
<head>
<meta charset="utf-8">
<title>Quella Staffing – Healthcare Recruitment Banner</title>
<link href="https://fonts.googleapis.com/css2?family=Poppins:wght@400;600;700;800&display=swap" rel="stylesheet">
<style>
  :root {
    --brand-blue: #2b34c9;
    --ink: #333333;
    --black: #111111;
    --paper: #ffffff;
    --panel-fill: #d4e7ef;
    --panel-fill-2: #bcd9e6;
    --footer-top: #3a3d42;
    --footer-bottom: #0c0c0e;
    --muted-line: #6d6d6d;
  }
  * { box-sizing: border-box; margin: 0; padding: 0; }
  html, body { width: 1200px; height: 4000px; overflow: hidden; background: var(--paper); }
  body { font-family: "Poppins", sans-serif; color: var(--ink); }
  .banner { position: relative; width: 1200px; height: 4000px; background: var(--paper); }
  .centered { position: absolute; left: 0; width: 1200px; text-align: center; }

  .brand-name { top: 250px; font-size: 96px; font-weight: 700; color: var(--black); letter-spacing: 4px; line-height: 1; }

  .headline-top { top: 520px; font-size: 150px; font-weight: 800; color: var(--brand-blue); line-height: 1; letter-spacing: -2px; }
  .headline-mid { top: 680px; font-size: 140px; font-weight: 800; color: var(--ink); line-height: 1; letter-spacing: -2px; }
  .headline-sub { top: 850px; font-size: 82px; font-weight: 700; color: var(--brand-blue); letter-spacing: 44px; padding-left: 44px; line-height: 1; }
  .dot-row { top: 985px; font-size: 40px; font-weight: 800; color: var(--ink); letter-spacing: 14px; padding-left: 14px; line-height: 1; }
  .tagline { top: 1050px; font-size: 80px; font-weight: 700; color: var(--ink); line-height: 1.15; }

  .scene { position: absolute; border: 4px solid var(--brand-blue); background: linear-gradient(180deg, var(--panel-fill), var(--panel-fill-2)); }
  .scene-left { left: 90px; top: 1420px; width: 330px; height: 730px; }
  .scene-mid { left: 435px; top: 1360px; width: 330px; height: 790px; }
  .scene-right { left: 780px; top: 1420px; width: 330px; height: 730px; }

  .section-title { top: 2320px; font-size: 88px; font-weight: 700; color: var(--brand-blue); letter-spacing: 22px; padding-left: 22px; line-height: 1; }
  .section-copy { top: 2450px; font-size: 60px; font-weight: 700; color: var(--black); line-height: 1.2; }

  .divider { position: absolute; left: 90px; top: 2740px; width: 1020px; border-top: 3px dashed var(--muted-line); }
  .specialty { position: absolute; top: 2800px; width: 320px; text-align: center; }
  .specialty svg { width: 110px; height: 110px; display: block; margin: 0 auto 20px; }
  .specialty-label { font-size: 54px; font-weight: 600; color: var(--black); line-height: 1.15; }
  .specialty-allied { left: 60px; }
  .specialty-nursing { left: 440px; }
  .specialty-medical { left: 820px; }
  .v-rule { position: absolute; top: 2790px; height: 300px; border-left: 3px dashed var(--muted-line); }
  .v-rule-a { left: 410px; }
  .v-rule-b { left: 790px; }

  .footer { position: absolute; left: 0; top: 3310px; width: 1200px; height: 690px; background: linear-gradient(180deg, var(--footer-top), var(--footer-bottom)); }
  .cta { position: absolute; left: 205px; top: 3240px; width: 790px; height: 130px; background: var(--brand-blue); border: 5px solid #ffffff; border-radius: 10px; color: #ffffff; font-size: 80px; font-weight: 700; letter-spacing: 14px; text-align: center; line-height: 120px; }
  .social { top: 3500px; font-size: 60px; color: #ffffff; line-height: 1; }
  .social .lead { font-weight: 400; }
  .social .dot { display: inline-block; width: 50px; height: 50px; border-radius: 50%; background: var(--brand-blue); vertical-align: -6px; margin: 0 18px 0 26px; }
  .social .handle { font-weight: 700; }
  .website { top: 3660px; font-size: 52px; color: #ffffff; letter-spacing: 10px; line-height: 1; }
  .website strong { font-weight: 700; }
</style>
</head>
<body>
<main class="banner">
  <div class="centered brand-name">Quella Staffing</div>

  <h1 class="centered headline-top">HEALTHCARE</h1>
  <div class="centered headline-mid">RECRUITMENT</div>
  <div class="centered headline-sub">AGENCY</div>
  <div class="centered dot-row">••••••</div>
  <p class="centered tagline">Empowering your next<br>career move</p>

  <div class="scene scene-left" role="img" aria-label="Illustration of a speech pathologist standing beside a child seated on a stool"></div>
  <div class="scene scene-mid" role="img" aria-label="Illustration of a doctor in a white coat and a nurse in teal scrubs holding a tablet"></div>
  <div class="scene scene-right" role="img" aria-label="Illustration of a physiotherapist guiding a patient exercising on a gym ball"></div>

  <h2 class="centered section-title">DISCOVER</h2>
  <p class="centered section-copy">Tailored opportunities based<br>on your career preference</p>

  <div class="divider"></div>

  <div class="specialty specialty-allied">
    <svg viewBox="0 0 100 100" aria-hidden="true">
      <path d="M50 88 L12 50 A22 22 0 0 1 50 18 A22 22 0 0 1 88 50 Z" fill="var(--brand-blue)"/>
      <polyline points="14,52 36,52 44,38 54,66 62,46 86,46" fill="none" stroke="#ffffff" stroke-width="6" stroke-linejoin="round" stroke-linecap="round"/>
    </svg>
    <div class="specialty-label">Allied<br>health</div>
  </div>
  <div class="v-rule v-rule-a"></div>
  <div class="specialty specialty-nursing">
    <svg viewBox="0 0 100 100" aria-hidden="true">
      <path d="M30 18 Q50 6 70 18 L68 32 L32 32 Z" fill="var(--brand-blue)"/>
      <rect x="46" y="14" width="8" height="14" fill="#ffffff"/>
      <rect x="43" y="17" width="14" height="8" fill="#ffffff"/>
      <circle cx="50" cy="44" r="14" fill="var(--brand-blue)"/>
      <path d="M18 96 Q18 64 50 62 Q82 64 82 96 Z" fill="var(--brand-blue)"/>
    </svg>
    <div class="specialty-label">Nursing</div>
  </div>
  <div class="v-rule v-rule-b"></div>
  <div class="specialty specialty-medical">
    <svg viewBox="0 0 100 100" aria-hidden="true">
      <circle cx="50" cy="50" r="40" fill="var(--brand-blue)"/>
      <circle cx="50" cy="50" r="31" fill="#ffffff"/>
      <rect x="40" y="26" width="20" height="48" rx="3" fill="var(--brand-blue)"/>
      <rect x="26" y="40" width="48" height="20" rx="3" fill="var(--brand-blue)"/>
    </svg>
    <div class="specialty-label">Medical</div>
  </div>

  <footer class="footer"></footer>
  <div class="cta">GET IN TOUCH</div>
  <div class="centered social"><span class="lead">Follow us on</span><span class="dot"></span><span class="handle">@quellastaffing</span></div>
  <div class="centered website">www.<strong>quellastaffing</strong>.com.au</div>
</main>
</body>
</html>
```